dsadasdasdasdsa

Industry/Entity Type

Mortgage Broking

Requirements
Must have
• Call-to-action button somewhere on the graphic
Nice to have
• The font of our logo is Montserrat

```html
<!DOCTYPE html>
<html lang="en">
<head>
<meta charset="utf-8">
<title>Mortgage Broker Directory Banner</title>
<link rel="stylesheet" href="https://fonts.googleapis.com/css2?family=Montserrat:wght@600;700;800;900&display=swap">
<style>
  :root {
    --green-deep: #0b4a2a;
    --green-mid: #1a7a45;
    --green-glow: #35a85e;
    --red-band: #9c2a1a;
    --red-dark: #5e1a10;
    --yellow: #f4ec1c;
    --white: #ffffff;
    --cta-light: #3fd16a;
    --cta-dark: #17a046;
    --cta-text: #0d2a16;
    --art-warm: #7a5a2e;
    --art-light: #5cbf5a;
  }
  * { margin: 0; padding: 0; box-sizing: border-box; }
  html, body {
    width: 1200px;
    height: 180px;
    overflow: hidden;
    background: var(--green-deep);
  }
  .banner {
    position: relative;
    width: 1200px;
    height: 180px;
    overflow: hidden;
    font-family: "Montserrat", sans-serif;
    background:
      radial-gradient(ellipse 520px 280px at 150px 90px, var(--green-glow) 0%, var(--green-mid) 40%, var(--green-deep) 100%);
  }
  .red-band {
    position: absolute;
    left: 300px;
    right: 0;
    top: 58px;
    height: 90px;
    background: linear-gradient(90deg, rgba(156,42,26,0) 0%, var(--red-band) 35%, var(--red-band) 75%, var(--red-dark) 100%);
  }
  .hero-art {
    position: absolute;
    left: 22px;
    top: 0;
    width: 268px;
    height: 180px;
    border-radius: 120px 120px 0 0;
    background: radial-gradient(ellipse at 50% 40%, var(--art-light) 0%, var(--art-light) 30%, var(--art-warm) 72%, rgba(122,90,46,0) 100%);
  }
  .headline {
    position: absolute;
    right: 29px;
    top: 5px;
    color: var(--yellow);
    font-weight: 700;
    font-size: 38px;
    letter-spacing: 0.3px;
    line-height: 44px;
    white-space: nowrap;
  }
  .search-text {
    position: absolute;
    right: 23px;
    top: 66px;
    text-align: right;
    color: var(--white);
    font-weight: 900;
    font-size: 40px;
    line-height: 37px;
    text-transform: uppercase;
    white-space: nowrap;
  }
  .cta-button {
    position: absolute;
    right: 0;
    top: 148px;
    width: 217px;
    height: 32px;
    border-radius: 16px 0 0 16px;
    background: linear-gradient(180deg, var(--cta-light) 0%, var(--cta-dark) 100%);
    color: var(--cta-text);
    font-weight: 900;
    font-size: 23px;
    line-height: 32px;
    text-align: center;
    text-decoration: none;
    text-transform: uppercase;
    letter-spacing: 0.5px;
    white-space: nowrap;
  }
</style>
</head>
<body>
  <div class="banner">
    <div class="red-band"></div>
    <div class="hero-art" role="img" aria-label="Illustration area"></div>
    <p class="headline">Need a Mortgage Broker?</p>
    <p class="search-text">Search now on Australia’s<br>largest directory</p>
    <a class="cta-button" href="#">Click here</a>
  </div>
</body>
</html>
```